Upscale business cards needed for Board of Directors

We need professional business cards created for members of our family business Board of Directors. We would like these relatively simple and straightforward, but also with a unique element to set them apart. Probably stick with neutral and simple colors - white, grey etc. We need space for the traditional elements, including name, title, address, email/phone number. And we will be creating several from this template so it needs to be template that is easy to switch information in and out of.
Business
See description

```html
<!DOCTYPE html>
<html lang="en">
<head>
<meta charset="UTF-8">
<title>Calder Holdings — Business Card</title>
<link href="https://fonts.googleapis.com/css2?family=Montserrat:wght@400;500;700&display=swap" rel="stylesheet">
<style>
  :root {
    --backdrop: #2e2e30;
    --gold: #bba77c;
    --gold-light: #cdbb93;
    --gold-dark: #a8946a;
    --ink: #231f20;
    --ink-soft: #2f2a2b;
    --paper: #ffffff;
    --text-light: #f2f2f2;
  }
  * { margin: 0; padding: 0; box-sizing: border-box; }
  html, body {
    width: 1200px;
    height: 843px;
    overflow: hidden;
    background: var(--backdrop);
    font-family: "Montserrat", Arial, sans-serif;
  }
  .stage {
    position: relative;
    width: 1200px;
    height: 843px;
  }
  .card {
    position: absolute;
    left: 320px;
    width: 560px;
    height: 320px;
    overflow: hidden;
    box-shadow: 0 10px 28px rgba(0,0,0,0.45);
  }

  /* Back side */
  .card--back {
    top: 81px;
    background: linear-gradient(120deg, var(--gold-dark), var(--gold-light) 55%, var(--gold));
    display: flex;
    align-items: center;
    justify-content: center;
  }
  .wordmark {
    font-weight: 700;
    text-transform: uppercase;
    text-align: center;
    line-height: 1;
  }
  .wordmark__name {
    display: block;
    font-size: 48px;
    letter-spacing: 1px;
  }
  .wordmark__sub {
    display: block;
    font-size: 17px;
    letter-spacing: 9px;
    margin-top: 8px;
  }
  .card--back .wordmark { color: var(--paper); }

  /* Front side */
  .card--front {
    top: 442px;
    background: var(--paper);
  }
  .front__header {
    position: absolute;
    left: 0; top: 0;
    width: 100%;
    height: 48%;
    background: var(--paper);
  }
  .card--front .wordmark {
    position: absolute;
    left: 48px;
    top: 48px;
    color: var(--ink);
    text-align: left;
  }
  .card--front .wordmark__name { font-size: 40px; }
  .card--front .wordmark__sub { font-size: 14px; letter-spacing: 8px; margin-left: 30px; }

  .front__band {
    position: absolute;
    left: 0; top: 48%;
    width: 100%;
    height: 38%;
    background: linear-gradient(180deg, var(--ink-soft), var(--ink));
  }
  .person {
    position: absolute;
    left: 28px;
    top: 16px;
  }
  .person__name {
    color: var(--gold);
    font-size: 16px;
    font-weight: 500;
    text-transform: uppercase;
    letter-spacing: 0.5px;
  }
  .person__title {
    color: var(--text-light);
    font-size: 12px;
    text-transform: uppercase;
    margin-top: 3px;
  }
  .contact {
    position: absolute;
    right: 30px;
    top: 30px;
    color: var(--text-light);
    font-size: 12px;
    line-height: 1.45;
  }
  .contact__label {
    color: var(--gold);
    font-weight: 700;
    margin-right: 4px;
  }
  .contact__gap { margin-top: 6px; }

  .front__strip {
    position: absolute;
    left: 0; bottom: 0;
    width: 100%;
    height: 14%;
    background: var(--gold);
    display: flex;
    align-items: center;
    padding-left: 36px;
  }
  .website {
    color: var(--paper);
    font-size: 12px;
    letter-spacing: 5px;
  }
</style>
</head>
<body>
  <main class="stage">
    <section class="card card--back" aria-label="Card back">
      <div class="wordmark">
        <span class="wordmark__name">Calder</span>
        <span class="wordmark__sub">Holdings</span>
      </div>
    </section>

    <section class="card card--front" aria-label="Card front">
      <div class="front__header">
        <div class="wordmark">
          <span class="wordmark__name">Calder</span>
          <span class="wordmark__sub">Holdings</span>
        </div>
      </div>
      <div class="front__band">
        <div class="person">
          <p class="person__name">Mark Ellison</p>
          <p class="person__title">President</p>
        </div>
        <div class="contact">
          <p>2170 Harbor View Lane</p>
          <p>Oak Ridge, NY 11020</p>
          <p class="contact__gap"><span class="contact__label">P :</span>555 0142 7788</p>
          <p><span class="contact__label">E :</span>mark@calderholdings.com</p>
        </div>
      </div>
      <div class="front__strip">
        <p class="website">www.calderholdings.com</p>
      </div>
    </section>
  </main>
</body>
</html>
```